In need of an AWESOME website for our Water Re-filling Store

The project is to design a website for our retail store front with the website www.quellbrookfillhouse.com. Currently if you go to that site it redirects you to our other site www.quellbrookbottleworks.com which is just our water bottle website. So, I need a new website created for www.quellbrookfillhouse.com (retail storefront)
Use our Squarespace to create a site with pages to help educate, tell about us, link to our water bottle brand site that is already created with Squarespace, and show the family and community aspects that we believe in. Our current water bottle website is www.quellbrookbottleworks.com for reference
We also sell hydration products, especially PRZQ products and have access to digital media through our PRZQ dealer site. we sell bottles, dispensers and other supplies for water refilling customers. We sell Ice as well.

Target Market(s)

Local residents looking to fill up their 1-5 gallon water jugs

Industry/Entity Type

Alkaline and Purified Water Retail Re-filling Store

Coding

Coded - Design and coding required

Font styles to use
Serif
Sans Serif

Colors
0054AA
0677BA
7BADD7
CADEEF
E8F1F8

Requirements
Must have
• pictures of our family in the about us section and pictures of our store inside and out.

```html
<!DOCTYPE html>
<html lang="en">
<head>
<meta charset="utf-8">
<title>Quellbrook Fill House</title>
<link href="https://fonts.googleapis.com/css2?family=Poppins:wght@400;500;600;700;800&family=Libre+Baskerville:wght@700&display=swap" rel="stylesheet">
<style>
:root{
  --hero-bg:#d6e0fa;
  --brand:#3152a3;
  --brand-dark:#1f3f94;
  --band:#3957a8;
  --ink:#2d2d2d;
  --white:#ffffff;
  --btn:#1d58b8;
}
*{box-sizing:border-box;margin:0;padding:0}
html,body{width:1200px;height:2853px;overflow:hidden}
body{position:relative;font-family:'Poppins',sans-serif;color:var(--ink);background:var(--white)}
.abs{position:absolute}
.hero{left:0;top:0;width:1200px;height:664px;background:var(--hero-bg)}
.logo{left:110px;top:34px;width:160px;text-align:center;color:var(--brand)}
.logo-name{font-size:22px;font-weight:600;line-height:1.1;letter-spacing:.5px}
.logo-dot{display:inline-block;width:26px;height:26px;border-radius:50%;background:var(--brand);margin-bottom:6px}
.logo-phone{font-family:'Libre Baskerville',serif;font-size:12px;margin-top:6px}
.nav{left:470px;top:34px;display:flex;gap:32px;font-size:14.5px;font-weight:500;color:#333}
.btn-store{left:978px;top:21px;width:160px;height:47px;background:var(--btn);color:var(--white);border:2px solid #1a3f8a;border-radius:3px;font-size:15.5px;font-weight:500;display:flex;align-items:center;justify-content:center}
.hero-title{right:62px;top:90px;text-align:right;font-size:38px;font-weight:800;line-height:1.02;color:var(--ink);letter-spacing:.3px}
.slide{left:111px;top:182px;width:894px;height:465px;background:linear-gradient(180deg,#b4a27c 0%,#a8946c 55%,#3d3a36 80%,#2a2a2a 100%)}
.arrow{width:50px;height:50px;border-radius:50%;background:var(--brand-dark);top:390px}
.section-title{font-size:40px;font-weight:700;line-height:1.08;color:var(--ink)}
.card-img{width:255px;height:335px}
.card-label{font-size:20px;font-weight:600;color:var(--ink)}
.band{left:0;top:1326px;width:1200px;height:474px;background:var(--band)}
.family{left:215px;top:1383px;width:294px;height:360px;background:linear-gradient(180deg,#c9c2b4 0%,#a79a86 60%,#6f5c48 100%)}
.about-title{left:594px;top:1405px;font-size:40px;font-weight:700;color:var(--white)}
.about-text{left:594px;top:1470px;width:500px;font-size:15.8px;line-height:24.7px;color:var(--white)}
.btn-learn{left:594px;top:1670px;width:160px;height:46px;background:var(--btn);border:2px solid #1a3f8a;border-radius:3px;color:var(--white);font-size:15px;font-weight:500;display:flex;align-items:center;justify-content:center}
.svc-label{font-size:19.5px;font-weight:600;color:var(--ink)}
.contact{left:0;top:2487px;width:1200px;height:366px;background:linear-gradient(135deg,#243f8f 0%,#2c4ea3 45%,#1e3a88 100%)}
.contact-title{left:113px;top:2573px;font-size:40px;font-weight:700;line-height:1.08;color:var(--white)}
.contact-line{left:113px;color:var(--white);font-size:20px;font-weight:600;line-height:25px}
.contact-mail{left:113px;top:2793px;color:var(--white);font-size:22px;font-weight:400}
</style>
</head>
<body>
<div class="abs hero"></div>
<div class="abs logo"><span class="logo-dot"></span><div class="logo-name">Quellbrook<br>Fill House</div><div class="logo-phone">520-555-0148</div></div>
<nav class="abs nav"><span>Home</span><span>About</span><span>Our Store</span><span>Products</span><span>Hydration Education</span></nav>
<div class="abs btn-store">Visit Our Store</div>
<h1 class="abs hero-title">HYDRATION STARTS<br>HERE</h1>
<div class="abs slide" role="img" aria-label="Storefront exterior with building sign and glass entry doors"></div>
<svg class="abs arrow" style="left:129px" viewBox="0 0 50 50"><path d="M33 25H17M24 18l-7 7 7 7" stroke="#fff" stroke-width="3" fill="none" stroke-linecap="round" stroke-linejoin="round"/></svg>
<svg class="abs arrow" style="left:1087px" viewBox="0 0 50 50"><path d="M17 25h16M26 18l7 7-7 7" stroke="#fff" stroke-width="3" fill="none" stroke-linecap="round" stroke-linejoin="round"/></svg>

<h2 class="abs section-title" style="left:110px;top:742px">Featured<br>Products</h2>
<div class="abs card-img" style="left:111px;top:864px;background:linear-gradient(180deg,#6d6a70,#9aa19c 50%,#3b3b3e)" role="img" aria-label="Cooler stocked with electrolyte drink cans"></div>
<div class="abs card-img" style="left:428px;top:864px;background:linear-gradient(180deg,#8c9096,#5e8fd0 45%,#3f79c6)" role="img" aria-label="Refillable five gallon water bottles"></div>
<div class="abs card-img" style="left:743px;top:864px;background:linear-gradient(180deg,#3d6fc2,#d7dde6 25%,#c2cad6 85%,#2a2a2a)" role="img" aria-label="Ice freezer with bagged ice"></div>
<div class="abs card-img" style="left:1059px;top:864px;background:linear-gradient(90deg,#a8a39a,#f4f4f4 55%,#e9e9e9)" role="img" aria-label="White water dispenser bottle"></div>
<div class="abs card-label" style="left:110px;top:1209px">PRZQ Electrolytes</div>
<div class="abs card-label" style="left:426px;top:1209px">Refillable Bottles</div>
<div class="abs card-label" style="left:742px;top:1209px">ICE</div>
<div class="abs card-label" style="left:1058px;top:1209px;white-space:nowrap">Water Dispensers</div>

<div class="abs band"></div>
<div class="abs family" role="img" aria-label="Family portrait at the beach"></div>
<h2 class="abs about-title">About Us</h2>
<p class="abs about-text">At Quellbrook Bottleworks Co., hydration goes far beyond simply quenching thirst; it represents a deep commitment to enhancing both personal health and environmental sustainability. Drawing inspiration from the resilient and vibrant spirit of Tucson, AZ, the brand delivers a premium alkaline water experience thoughtfully designed to meet the needs of today's health-conscious and eco-aware consumers.</p>
<div class="abs btn-learn">Learn More</div>

<h2 class="abs section-title" style="left:113px;top:1876px">Our<br>Services</h2>
<div class="abs card-img" style="left:73px;top:2017px;background:linear-gradient(180deg,#4b5f7e,#4f82c9 55%,#2e5fa8)" role="img" aria-label="Water refill jugs with splash"></div>
<div class="abs card-img" style="left:340px;top:2017px;background:linear-gradient(180deg,#3d6fc2,#d7dde6 25%,#c2cad6 85%,#2a2a2a)" role="img" aria-label="Ice freezer with bagged ice"></div>
<div class="abs card-img" style="left:606px;top:2017px;background:linear-gradient(180deg,#2f4f97,#26407f 50%,#1c2f6a)" role="img" aria-label="Event booth with blue canopy and products"></div>
<div class="abs card-img" style="left:873px;top:2017px;background:linear-gradient(180deg,#b9ab92,#8b8375 50%,#d9d9dc)" role="img" aria-label="Owners standing behind cases of bottles"></div>
<div class="abs svc-label" style="left:73px;top:2365px">WATER REFILLS</div>
<div class="abs svc-label" style="left:339px;top:2365px">ICE</div>
<div class="abs svc-label" style="left:605px;top:2365px">HYDRATION PRODUCTS</div>
<div class="abs svc-label" style="left:872px;top:2365px">EQUIPMENT &amp; SUPPLIES</div>

<div class="abs contact"></div>
<h2 class="abs contact-title">Contact<br>Us</h2>
<div class="abs contact-line" style="top:2671px">4821 Clearspring Lane<br>Tucson, AZ 857XX</div>
<div class="abs contact-line" style="top:2749px;font-size:21px">(520) 555-0193</div>
<div class="abs contact-mail">sales@quellbrookfillhouse.com</div>
</body>
</html>
```